Corvane Capital Business Cards

These are professional business cards that are for my family office.
Put fake emails and phone numbers as of now until I finalize those components. This family office controls my families investments, assets, and future. The cards should be professional.
..
.
.
.
I just uploaded another variation of a logo I would like to see as a business card to I am inbeteen which logo to use

Target Market(s)

business

Industry/Entity Type

business

Contact Information for Business Card

Professional, wealth related, finance related.

Requirements
Must have
• Logo

```html
<!DOCTYPE html>
<html lang="en">
<head>
<meta charset="utf-8">
<title>Corvane Capital Business Cards</title>
<link href="https://fonts.googleapis.com/css2?family=Playfair+Display:wght@400&family=Lato:wght@400;700&display=swap" rel="stylesheet">
<style>
  :root {
    --stage: #1b1b1b;
    --ink: #000000;
    --paper: #ffffff;
    --gold: #c2a86a;
    --divider: #5a4d2e;
  }
  * { box-sizing: border-box; margin: 0; padding: 0; }
  html, body {
    width: 1200px;
    height: 1015px;
    overflow: hidden;
    background: var(--stage);
  }
  .stage {
    width: 1200px;
    height: 1015px;
    display: flex;
    flex-direction: column;
    align-items: center;
    justify-content: center;
    gap: 44px;
  }
  .card {
    position: relative;
    width: 760px;
    height: 434px;
    overflow: hidden;
  }
  .wordmark {
    font-family: "Playfair Display", Georgia, serif;
    font-weight: 400;
    font-size: 50px;
    letter-spacing: 0.08em;
    white-space: nowrap;
  }

  /* Front */
  .card--front { background: var(--ink); }
  .card--front .wordmark {
    position: absolute;
    left: 0; right: 0;
    top: 170px;
    text-align: center;
    color: var(--gold);
  }
  .card--front .rule {
    position: absolute;
    left: 0; right: 0;
    bottom: 12px;
    height: 5px;
    background: var(--gold);
  }

  /* Back */
  .card--back { background: var(--ink); }
  .back__top {
    position: absolute;
    left: 0; right: 0; top: 0;
    height: 258px;
    background: var(--paper);
    border-bottom: 4px solid var(--gold);
    box-shadow: 0 4px 0 var(--paper);
  }
  .back__top .wordmark {
    position: absolute;
    left: 0; right: 0;
    top: 150px;
    text-align: center;
    color: var(--ink);
  }
  .back__info {
    position: absolute;
    left: 0; right: 0;
    top: 280px;
    display: grid;
    grid-template-columns: 1fr auto 1fr;
    column-gap: 26px;
    align-items: center;
    padding: 0 40px;
  }
  .person { text-align: right; }
  .person__name {
    font-family: "Playfair Display", Georgia, serif;
    font-size: 25px;
    letter-spacing: 0.06em;
    color: var(--gold);
    text-transform: uppercase;
    line-height: 1.1;
  }
  .person__role {
    font-family: "Lato", Arial, sans-serif;
    font-size: 18px;
    color: var(--paper);
    letter-spacing: 0.02em;
    margin-top: 2px;
  }
  .divider {
    width: 1px;
    height: 78px;
    background: var(--divider);
  }
  .contact { list-style: none; }
  .contact li {
    display: flex;
    align-items: center;
    gap: 10px;
    font-family: "Lato", Arial, sans-serif;
    font-size: 17px;
    color: var(--paper);
    line-height: 26px;
    letter-spacing: 0.02em;
  }
  .contact svg { width: 17px; height: 17px; flex: none; }
  .address {
    position: absolute;
    left: 0; right: 0;
    top: 380px;
    text-align: center;
    font-family: "Lato", Arial, sans-serif;
    font-size: 18px;
    color: var(--paper);
    letter-spacing: 0.02em;
  }
</style>
</head>
<body>
<main class="stage">
  <section class="card card--front" aria-label="Card front">
    <p class="wordmark">CORVANE CAPITAL</p>
    <div class="rule"></div>
  </section>

  <section class="card card--back" aria-label="Card back">
    <div class="back__top">
      <p class="wordmark">CORVANE CAPITAL</p>
    </div>
    <div class="back__info">
      <div class="person">
        <p class="person__name">Elias Marlowe</p>
        <p class="person__role">Managing Director</p>
      </div>
      <div class="divider"></div>
      <ul class="contact">
        <li>
          <svg viewBox="0 0 24 24" aria-hidden="true"><path fill="var(--gold)" d="M6.6 10.8a15.1 15.1 0 0 0 6.6 6.6l2.2-2.2a1 1 0 0 1 1-.25 11.4 11.4 0 0 0 3.6.57 1 1 0 0 1 1 1V20a1 1 0 0 1-1 1A17 17 0 0 1 3 4a1 1 0 0 1 1-1h3.5a1 1 0 0 1 1 1c0 1.25.2 2.45.57 3.57a1 1 0 0 1-.25 1z"/></svg>
          055-210 987 654
        </li>
        <li>
          <svg viewBox="0 0 24 24" aria-hidden="true"><path fill="var(--gold)" d="M2 5h20v14H2zm2 2v.4l8 5.2 8-5.2V7zm0 2.8V17h16V9.8l-8 5.2z"/></svg>
          hello@corvanecap.com
        </li>
        <li>
          <svg viewBox="0 0 24 24" aria-hidden="true"><g fill="none" stroke="var(--gold)" stroke-width="2"><circle cx="12" cy="12" r="9.5"/><ellipse cx="12" cy="12" rx="4" ry="9.5"/><path d="M2.5 12h19M4 7h16M4 17h16"/></g></svg>
          www.corvanecap.com
        </li>
      </ul>
    </div>
    <p class="address">18 Harbour Row, Westbridge, 40917</p>
  </section>
</main>
</body>
</html>
```